Corbell Lending Partners - Real estate loans - need a business card with a logo

I need a logo and a business card that looks elegant - that looks as if it is a big stablish corporation - We do real estate loans, my goal is to brand myself with colors black background - gold or silver letters - some combination - Name of the company different color than the rest of the card -

```html
<!DOCTYPE html>
<html lang="en">
<head>
<meta charset="utf-8">
<title>Corbell Lending Partners – Business Card</title>
<link rel="stylesheet" href="https://fonts.googleapis.com/css2?family=Montserrat:wght@400;500;700&display=swap">
<style>
  :root {
    --backdrop: #151515;
    --backdrop-edge: #0b0b0b;
    --card: #1d1d1d;
    --card-sheen: #2a2a2a;
    --gold: #d8b67f;
    --ink-light: #ececec;
  }
  * { box-sizing: border-box; margin: 0; padding: 0; }
  html, body {
    width: 1200px;
    height: 900px;
    overflow: hidden;
  }
  body {
    background: radial-gradient(ellipse at 60% 45%, var(--backdrop) 0%, var(--backdrop-edge) 100%);
    font-family: "Montserrat", sans-serif;
    position: relative;
  }
  .card {
    position: absolute;
    left: 250px;
    width: 700px;
    height: 400px;
    background: linear-gradient(135deg, var(--card) 0%, var(--card) 55%, var(--card-sheen) 80%, var(--card) 100%);
    box-shadow: 0 18px 40px rgba(0, 0, 0, 0.6);
  }
  .card-front { top: 40px; }
  .card-back { top: 460px; }

  .brand {
    display: flex;
    align-items: center;
    gap: 16px;
    color: var(--gold);
  }
  .brand-square {
    width: 22px;
    height: 22px;
    background: var(--gold);
    flex: none;
  }
  .brand-name {
    font-weight: 700;
    letter-spacing: 0.5px;
    white-space: nowrap;
  }

  .card-front .brand {
    position: absolute;
    left: 0;
    right: 0;
    top: 0;
    bottom: 0;
    justify-content: center;
  }
  .card-front .brand-name { font-size: 36px; }

  .card-back .brand {
    position: absolute;
    left: 48px;
    top: 56px;
  }
  .card-back .brand-name { font-size: 30px; }

  .person {
    position: absolute;
    left: 48px;
    top: 200px;
  }
  .person-name {
    color: var(--gold);
    font-weight: 700;
    font-size: 24px;
  }
  .person-title {
    color: var(--ink-light);
    font-size: 17px;
    margin-top: 2px;
  }
  .divider {
    position: absolute;
    left: 48px;
    top: 282px;
    width: 500px;
    height: 1px;
    background: var(--gold);
  }
  .contact {
    position: absolute;
    left: 48px;
    top: 302px;
    color: var(--ink-light);
    font-size: 17px;
    line-height: 1.6;
    letter-spacing: 0.4px;
  }
  .contact-label {
    color: var(--gold);
    font-weight: 700;
  }
</style>
</head>
<body>
  <section class="card card-front">
    <div class="brand">
      <span class="brand-square"></span>
      <span class="brand-name">Corbell Lending Partners</span>
    </div>
  </section>

  <section class="card card-back">
    <div class="brand">
      <span class="brand-square"></span>
      <span class="brand-name">Corbell Lending Partners</span>
    </div>
    <div class="person">
      <p class="person-name">Marcus Hale</p>
      <p class="person-title">Director</p>
    </div>
    <div class="divider"></div>
    <div class="contact">
      <p><span class="contact-label">P :</span> (555) 214-3308 | <span class="contact-label">E :</span> info@corbellending.com</p>
      <p>www.corbellending.com</p>
    </div>
  </section>
</body>
</html>
```